Business Card Design Project

This is the first time we use our new logo. We need a business card that we can use both on our institutional corporate relationships and also that works for our staff that deals with consumers directly.

VELUNDA is a new company dedicated to empower consumers and to provide them with the best choices for specialized health care using the latest telemedicine technology (medicine at a distance via videoconference).

We want to print this cards in high quality materials and process. We will like designs that allow us to use UV spot varnish and other techniques that will differentiate us.

We are including Two different versions of Color logos. In addition we are including white over black background logos. Those can be used replacing the black for a color.

Please note this is the first time we will be creating any corporate materials with our new logo and colors.

Target Market(s)

34+ consumers of medium high and high socioeconomic levels.

Industry/Entity Type

Health

Requirements
Must have
• Our logo on its original colors
Should not have
• Any other graphical element or design that is not our logo

```html
<!DOCTYPE html>
<html lang="en">
<head>
<meta charset="utf-8">
<title>VELUNDA Business Card</title>
<link rel="stylesheet" href="https://fonts.googleapis.com/css2?family=Montserrat:wght@400;600;700&family=Arimo:wght@400&display=swap">
<style>
  :root {
    --bg: #e9e9ee;
    --brand-blue: #1b557f;
    --accent-teal: #14a596;
    --accent-sky: #58b4e0;
    --paper: #ffffff;
    --ink: #1a1a1a;
    --icon: #4a4f57;
  }
  * { margin: 0; padding: 0; box-sizing: border-box; }
  html, body {
    width: 1200px; height: 987px; overflow: hidden;
    background: var(--bg);
  }
  .canvas { position: relative; width: 1200px; height: 987px; }

  .card {
    position: absolute;
    width: 560px; height: 320px;
    border-radius: 30px;
    overflow: hidden;
    box-shadow: 0 6px 18px rgba(0,0,0,0.12);
  }

  /* Back side */
  .card-back {
    left: 580px; top: 90px;
    background: var(--brand-blue);
    color: var(--paper);
    display: flex; flex-direction: column; align-items: center; justify-content: center;
  }
  .back-wordmark {
    font-family: "Montserrat", sans-serif;
    font-weight: 700;
    font-size: 54px;
    letter-spacing: 4px;
  }
  .back-url {
    margin-top: 22px;
    font-family: "Montserrat", sans-serif;
    font-weight: 400;
    font-size: 17px;
    letter-spacing: 5px;
  }
  .back-url strong { font-weight: 700; }

  /* Front side */
  .card-front {
    left: 50px; top: 520px;
    background: var(--paper);
  }
  .front-wave { position: absolute; inset: 0; width: 100%; height: 100%; }

  .wordmark {
    position: absolute; left: 238px; top: 108px;
    font-family: "Montserrat", sans-serif;
    font-weight: 700;
    font-size: 46px;
    letter-spacing: 3px;
    color: var(--brand-blue);
  }

  .contact-list {
    position: absolute; left: 34px; top: 44px;
    list-style: none;
    font-family: "Arimo", sans-serif;
    font-size: 14px;
    line-height: 19px;
    color: var(--ink);
  }
  .contact-list li { display: flex; align-items: center; gap: 6px; }
  .contact-list .icon { width: 12px; height: 12px; flex: none; }
  .contact-list .address { padding-left: 0; }

  .holder {
    position: absolute; right: 30px; bottom: 14px;
    text-align: right;
    color: var(--paper);
    font-family: "Montserrat", sans-serif;
  }
  .holder-name { font-weight: 700; font-size: 26px; line-height: 30px; }
  .holder-title { font-weight: 400; font-size: 17px; line-height: 22px; }
</style>
</head>
<body>
<main class="canvas">

  <section class="card card-back" aria-label="Card back">
    <div class="back-wordmark">VELUNDA</div>
    <div class="back-url">www.<strong>velunda</strong>.com</div>
  </section>

  <section class="card card-front" aria-label="Card front">
    <svg class="front-wave" viewBox="0 0 560 320" preserveAspectRatio="none" aria-hidden="true">
      <path d="M0,175 C40,265 180,290 320,262 C420,244 500,240 560,248 L560,320 L0,320 Z" fill="var(--brand-blue)"/>
      <path d="M0,160 C30,240 90,285 150,300" fill="none" stroke="var(--accent-sky)" stroke-width="4"/>
      <path d="M300,258 C400,236 480,238 560,262" fill="none" stroke="var(--accent-teal)" stroke-width="6"/>
    </svg>

    <div class="wordmark">VELUNDA</div>

    <ul class="contact-list">
      <li>
        <svg class="icon" viewBox="0 0 12 12" aria-hidden="true"><circle cx="6" cy="6" r="6" fill="var(--icon)"/><path d="M4 3.2 L5 3 L5.6 4.6 L5 5.2 C5.4 6 6 6.6 6.8 7 L7.4 6.4 L9 7 L8.8 8 C6 8.4 3.6 6 4 3.2Z" fill="#fff"/></svg>
        012-345-6789
      </li>
      <li>
        <svg class="icon" viewBox="0 0 12 12" aria-hidden="true"><circle cx="6" cy="6" r="6" fill="var(--icon)"/><path d="M4 3.2 L5 3 L5.6 4.6 L5 5.2 C5.4 6 6 6.6 6.8 7 L7.4 6.4 L9 7 L8.8 8 C6 8.4 3.6 6 4 3.2Z" fill="#fff"/></svg>
        012-345-6789
      </li>
      <li>
        <svg class="icon" viewBox="0 0 12 12" aria-hidden="true"><circle cx="6" cy="6" r="6" fill="var(--icon)"/><rect x="2.8" y="3.8" width="6.4" height="4.4" fill="#fff"/><path d="M2.8 3.8 L6 6.4 L9.2 3.8" fill="none" stroke="var(--icon)" stroke-width="0.8"/></svg>
        name@velunda.com
      </li>
      <li>
        <svg class="icon" viewBox="0 0 12 12" aria-hidden="true"><circle cx="6" cy="6" r="6" fill="var(--icon)"/><circle cx="6" cy="6" r="3.6" fill="none" stroke="#fff" stroke-width="0.8"/><path d="M2.4 6 H9.6 M6 2.4 V9.6" stroke="#fff" stroke-width="0.8"/></svg>
        www.velunda.com
      </li>
      <li class="address">Street Name, City Name</li>
      <li class="address">State, City Zip Code</li>
    </ul>

    <div class="holder">
      <div class="holder-name">Your Name</div>
      <div class="holder-title">Title</div>
    </div>
  </section>

</main>
</body>
</html>
```